Book Cover Design RTM

Want a new book cover but want to use the same photo and change the sub name. This is for a brand called "Amber Meadow Living". The book is called "Quiet Steps, Bright Days"

This is for a 8.5 * 11 book size

We really want to brand the Amber Meadow Living

I've attached a sample of an old book cover, the photo I want used and the amber meadow living logo

Requirements
Must have
• Must have the logo,

must have the book title. "Quiet Steps, Bright Days"

Must have "Featuring" The Amber Meadow Living Tumble Card Game"

On the back put the logo and Amber Meadow Living Nutrition

must have the authors name "Norma Plaskett" on the page

"The Golden Stride Map"
Nice to have
• Amber Meadow Living Presents:

the book title

```html
<!DOCTYPE html>
<html lang="en">
<head>
<meta charset="utf-8">
<title>Quiet Steps, Bright Days — Book Cover Spread</title>
<link href="https://fonts.googleapis.com/css2?family=Bebas+Neue&family=Montserrat:wght@400;700&family=Oswald:wght@400;500&display=swap" rel="stylesheet">
<style>
  :root {
    --backdrop: #153033;
    --cover-black: #0a0b0b;
    --mint: #8fdcc5;
    --mint-soft: #6fbfa9;
    --white: #f4f4f2;
    --grey: #b9bdbc;
  }
  * { box-sizing: border-box; margin: 0; padding: 0; }
  html, body {
    width: 1200px; height: 900px; overflow: hidden;
    background: var(--backdrop);
  }
  .spread {
    position: absolute; left: 189px; top: 131px;
    width: 822px; height: 637px;
    display: flex;
  }
  .cover {
    position: relative; width: 400px; height: 637px;
    background: var(--cover-black); overflow: hidden;
  }
  /* Front cover */
  .cover-photo {
    position: absolute; left: 90px; top: 0; width: 310px; height: 637px;
    background:
      radial-gradient(circle at 28% 44%, #7fc3ad 0, #5c9b89 22%, rgba(10,11,11,0) 40%),
      radial-gradient(ellipse at 68% 45%, #4a3128 0, #2a1c17 30%, rgba(10,11,11,0) 60%);
  }
  .series {
    position: absolute; left: 29px; top: 44px;
    font-family: "Montserrat", sans-serif; color: var(--white);
    font-size: 17px; line-height: 22px; letter-spacing: 0.2px;
  }
  .series strong { font-weight: 700; display: block; }
  .series-rule {
    position: absolute; left: 29px; top: 113px; width: 142px; height: 2px;
    background: var(--mint);
  }
  .author-line {
    position: absolute; left: 29px; top: 122px;
    font-family: "Montserrat", sans-serif; color: var(--mint);
    font-size: 21px;
  }
  .brand-mark {
    position: absolute; left: 70px; top: 262px; width: 200px;
    text-align: center;
    font-family: "Montserrat", sans-serif; font-weight: 700;
    color: var(--cover-black); font-size: 14px; letter-spacing: 1.5px;
    text-transform: uppercase; line-height: 1.3;
  }
  .title {
    position: absolute; left: 28px; top: 312px; width: 360px;
    font-family: "Bebas Neue", sans-serif; color: var(--white);
    font-size: 86px; line-height: 0.98; letter-spacing: 0.5px;
  }
  .featuring {
    position: absolute; left: 29px; top: 513px; width: 200px;
    border-top: 2px solid var(--mint-soft);
    border-bottom: 2px solid var(--mint-soft);
    padding: 9px 0 6px;
    font-family: "Oswald", sans-serif;
  }
  .featuring .label { color: var(--mint); font-weight: 500; font-size: 16px; text-transform: uppercase; }
  .featuring .game { color: var(--white); font-size: 14px; text-transform: uppercase; line-height: 1.25; margin-top: 2px; }
  .featuring .game em { font-style: normal; color: var(--mint); font-weight: 500; font-size: 19px; display: block; }

  /* Spine */
  .spine {
    width: 22px; height: 637px; background: #050505;
    display: flex; justify-content: center;
  }
  .spine-inner {
    writing-mode: vertical-rl; transform: rotate(180deg);
    height: 100%; display: flex; justify-content: space-between; align-items: center;
    padding: 40px 0 28px;
    color: var(--white);
  }
  .spine-author { font-family: "Montserrat", sans-serif; font-size: 9px; letter-spacing: 2px; color: var(--grey); }
  .spine-title { font-family: "Montserrat", sans-serif; font-weight: 700; font-size: 12px; letter-spacing: 2px; margin-top: 60px; }
  .spine-brand { font-family: "Montserrat", sans-serif; font-size: 7px; letter-spacing: 1.5px; color: var(--grey); }

  /* Back cover */
  .back-brand {
    position: absolute; left: 0; top: 92px; width: 100%;
    text-align: center;
    font-family: "Montserrat", sans-serif; font-weight: 700;
    color: var(--white); font-size: 19px; letter-spacing: 2px;
    text-transform: uppercase;
  }
  .affirmations {
    position: absolute; left: 0; top: 188px; width: 100%;
    list-style: none; text-align: center;
    font-family: "Bebas Neue", sans-serif; color: var(--white);
    font-size: 32px; line-height: 40px;
  }
</style>
</head>
<body>
  <main class="spread">
    <section class="cover cover-front">
      <div class="cover-photo" role="img" aria-label="Photo of the author in workout wear, leaning on a mint exercise ball"></div>
      <p class="series">YOUR<strong>GOLDEN STRIDE</strong>MAP</p>
      <div class="series-rule"></div>
      <p class="author-line">by NORMA PLASKETT</p>
      <p class="brand-mark">Amber Meadow Living</p>
      <h1 class="title">QUIET STEPS,<br>BRIGHT DAYS</h1>
      <div class="featuring">
        <p class="label">Featuring:</p>
        <p class="game">“The Amber Meadow Living<em>Tumble Card Game”</em></p>
      </div>
    </section>

    <section class="spine">
      <div class="spine-inner">
        <span class="spine-author">NORMA PLASKETT</span>
        <span class="spine-title">QUIET STEPS BRIGHT DAYS</span>
        <span class="spine-brand">AMBER MEADOW LIVING</span>
      </div>
    </section>

    <section class="cover cover-back">
      <p class="back-brand">Amber Meadow Living</p>
      <ul class="affirmations">
        <li>I crush my goals</li>
        <li>I persever</li>
        <li>I take decsive action</li>
        <li>I am deliberate</li>
        <li>I hold my head high</li>
        <li>I don’t quit</li>
        <li>I am formidable</li>
        <li>I am secure</li>
        <li>I am motivated</li>
        <li>I am loved</li>
      </ul>
    </section>
  </main>
</body>
</html>
```